Business Card Re-Design/Update

We'd like to update out business cards. I've included our current "Style guide" which has the colour scheme of the organisation in it. I've also included the branding files with logos etc in them.

I've also included a copy of one of our existing cards so that you can see how ugly/dated they look. I'd like a fresh modern corporate look.

Target Market(s)

These are for our clients, potential clients, industry contacts - like all business cards

Contact Information for Business Card

Name
Position
Company Address - Level 1, 47 Fernby Street, Carlow Qld 4072
Direct Phone
mobile
Email
Website -www.korvalit.com.au
Logo

Colors

Designer to choose colors to be used in the design.

Requirements
Must have
• Main Logo
• Cards will need to be editable to be able to personalize them for each new employee.
Nice to have
• The MapOut, ShipWell, KeepSteady would be okay to have if they can be sensibly and professionally added to the look without detracting from the main imagery.
• Maybe they could go on the back of the card? will leave this to your creative discretion as to whether/where they fit.
Should not have
• Should not have decorative or script fonts

```html
<!DOCTYPE html>
<html lang="en">
<head>
<meta charset="utf-8">
<title>korvalIT – Business Card</title>
<link rel="stylesheet" href="https://fonts.googleapis.com/css2?family=Work+Sans:wght@400;500&display=swap">
<style>
  :root {
    --page-bg: #e9e6e2;
    --card-bg: #3c3a39;
    --brand-blue: #2b8ab5;
    --text-light: #c9c2ba;
    --icon-grey: #8f8a85;
  }
  * { margin: 0; padding: 0; box-sizing: border-box; }
  html, body {
    width: 1200px; height: 1047px; overflow: hidden;
    background: var(--page-bg);
    font-family: "Work Sans", Arial, sans-serif;
  }
  .card {
    position: absolute; left: 120px; top: 262px;
    width: 960px; height: 524px;
    background: var(--card-bg);
    border-radius: 22px;
    box-shadow: 0 14px 40px rgba(0,0,0,0.18);
    overflow: hidden;
  }
  .brand {
    position: absolute; left: 52px; top: 40px;
    display: flex; align-items: center; gap: 14px;
  }
  .brand-dot {
    width: 30px; height: 30px; border-radius: 50%;
    background: var(--brand-blue);
  }
  .brand-name {
    font-size: 46px; font-weight: 500; color: var(--brand-blue);
    letter-spacing: 0.5px; line-height: 1;
  }
  .person-name {
    position: absolute; left: 52px; top: 150px;
    font-size: 36px; font-weight: 500; color: var(--brand-blue);
    letter-spacing: 1px; line-height: 1;
  }
  .person-role {
    position: absolute; left: 52px; top: 196px;
    font-size: 21px; color: var(--text-light); letter-spacing: 0.6px;
  }
  .address {
    position: absolute; left: 52px; top: 246px;
    font-size: 21px; line-height: 29px; color: var(--text-light);
    letter-spacing: 0.6px; font-style: normal;
  }
  .contact-list {
    position: absolute; left: 52px; top: 322px;
    list-style: none;
  }
  .contact-list li {
    display: flex; align-items: center; gap: 10px;
    height: 29px;
    font-size: 21px; color: var(--text-light); letter-spacing: 0.6px;
  }
  .contact-icon { width: 16px; height: 16px; flex: none; }
  .contact-icon * { fill: none; stroke: var(--icon-grey); stroke-width: 1.6; }
  .web-accent { color: var(--brand-blue); }
  .brand-emblem {
    position: absolute; left: 500px; top: 70px;
    width: 390px; height: 390px; border-radius: 50%;
    background: var(--brand-blue);
  }
</style>
</head>
<body>
  <main class="card">
    <div class="brand">
      <span class="brand-dot"></span>
      <span class="brand-name">korvalIT</span>
    </div>

    <h1 class="person-name">MARA WHITLOCK</h1>
    <p class="person-role">Business Development Manager</p>

    <address class="address">22/8 Harlow Bridge Road,<br>Kenmore QLD 4069</address>

    <ul class="contact-list">
      <li>
        <svg class="contact-icon" viewBox="0 0 16 16"><rect x="4" y="1.5" width="8" height="13" rx="1.5"/><line x1="7" y1="12" x2="9" y2="12"/></svg>
        +61 (0)400 555 018
      </li>
      <li>
        <svg class="contact-icon" viewBox="0 0 16 16"><path d="M2 6 Q8 1 14 6 L12 8 L10 6.5 L6 6.5 L4 8 Z"/><rect x="4" y="9" width="8" height="5" rx="1"/></svg>
        +61 (0)7 5550 1416
      </li>
      <li>
        <svg class="contact-icon" viewBox="0 0 16 16"><path d="M4 2 L6.5 5 L5 7 Q6.5 10 9 11 L11 9.5 L14 12 L12 14 Q5 13 2 4 Z"/></svg>
        +61 (0)7 5550 1433
      </li>
      <li>
        <svg class="contact-icon" viewBox="0 0 16 16"><rect x="4" y="2" width="8" height="4"/><rect x="2" y="6" width="12" height="6" rx="1"/><rect x="4" y="10" width="8" height="4"/></svg>
        +61 (0)7 5550 1403
      </li>
      <li>
        <svg class="contact-icon" viewBox="0 0 16 16"><rect x="2" y="4" width="12" height="9" rx="1"/><path d="M2 5 L8 9.5 L14 5"/></svg>
        mwhitlock@korvalit.com.au
      </li>
      <li>
        <svg class="contact-icon" viewBox="0 0 16 16"><circle cx="8" cy="8" r="6"/><ellipse cx="8" cy="8" rx="2.5" ry="6"/><line x1="2" y1="8" x2="14" y2="8"/></svg>
        www.<span class="web-accent">korvalit</span>.com.au
      </li>
    </ul>

    <div class="brand-emblem" role="img" aria-label="Large brand emblem area"></div>
  </main>
</body>
</html>
```